Lawn care business card

I am looking for a quality designed personal business card to represent the quality and elegant nature of our company. We separate ourselves in our market by the aesthetic value of our work, so I am looking for marketing material that does the same. We target our marketing high end customers, and we try to avoid price shoppers. I am open to all design options, so long as they are in line with our companies values.

We are tend to go with a retro look on everything from our logo and print material, to our uniforms. We like to portray and "old fashion" set of core values, with a modern elegance. So a wild and crazy look is out of the question.

Things I'd like on the card:
1.) Logo
2.) Phone number: (816) 555-2931
3.) Website: Verdelynkc.com
4.) Email: robertfairley@verdelynkc.com
5.) My name: Robert Fairley
6.) Facebook link: facebook.com/VerdelynGardenandGrounds
7.) Instagram: http://instagram.com/verdelynkc

Attached is a copy of our logo.

Reason: More time is needed to gather conclusive feedback from the members of our marketing team.

```html
<!DOCTYPE html>
<html lang="en">
<head>
<meta charset="utf-8">
<title>Verdelyn Garden &amp; Grounds — Business Card</title>
<link href="https://fonts.googleapis.com/css2?family=Arimo:wght@400;700&display=swap" rel="stylesheet">
<style>
  :root {
    --page: #e9e6e1;
    --card: #ffffff;
    --ink: #1c1c1c;
    --accent: #e8561c;
    --lawn-light: #5fae3a;
    --lawn-mid: #3f8a2a;
    --lawn-dark: #1f3a1c;
    --name: #ffffff;
  }
  * { box-sizing: border-box; margin: 0; padding: 0; }
  html, body { width: 1200px; height: 800px; overflow: hidden; }
  body {
    background: var(--page);
    font-family: "Arimo", Arial, sans-serif;
    position: relative;
  }
  .card {
    position: absolute;
    left: 75px; top: 100px;
    width: 1050px; height: 600px;
    background: var(--card);
    overflow: hidden;
    box-shadow: 0 10px 30px rgba(0,0,0,.18);
  }
  .card__art { position: absolute; inset: 0; }
  .card__name {
    position: absolute;
    left: 610px; top: 64px;
    color: var(--name);
    font-size: 48px;
    font-weight: 400;
    letter-spacing: 1px;
    white-space: nowrap;
  }
  .brand {
    position: absolute;
    left: 70px; top: 70px;
    display: flex; align-items: center; gap: 18px;
  }
  .brand__mark {
    width: 56px; height: 56px; border-radius: 50%;
    background: var(--accent);
  }
  .brand__name {
    font-size: 52px; font-weight: 700; color: var(--ink);
    letter-spacing: 1px;
  }
  .contacts {
    position: absolute;
    left: 70px; top: 250px;
    list-style: none;
  }
  .contacts__item {
    display: flex; align-items: center; gap: 22px;
    font-size: 27px; color: var(--ink);
    height: 52px;
    white-space: nowrap;
  }
  .contacts__icon {
    width: 28px; height: 28px; flex: none;
    background: var(--accent);
    display: flex; align-items: center; justify-content: center;
  }
  .contacts__icon svg { width: 18px; height: 18px; }
</style>
</head>
<body>
  <div class="card">
    <svg class="card__art" viewBox="0 0 1050 600" width="1050" height="600">
      <defs>
        <linearGradient id="lawn" x1="0" y1="0" x2="0" y2="1">
          <stop offset="0" stop-color="var(--lawn-dark)"/>
          <stop offset="0.3" stop-color="var(--lawn-mid)"/>
          <stop offset="1" stop-color="var(--lawn-light)"/>
        </linearGradient>
      </defs>
      <path class="card__band" d="M440,0 C540,130 690,440 1050,555 L1050,0 Z" fill="var(--accent)"/>
      <path class="card__photo" role="img" aria-label="Photo of a red riding mower on a freshly cut green lawn"
            d="M470,0 C565,120 710,420 1050,528 L1050,0 Z" fill="url(#lawn)"/>
    </svg>

    <div class="card__name">Robert Fairley</div>

    <div class="brand">
      <span class="brand__mark"></span>
      <span class="brand__name">VERDELYN</span>
    </div>

    <ul class="contacts">
      <li class="contacts__item">
        <span class="contacts__icon"><svg viewBox="0 0 24 24"><path fill="#fff" d="M6.6 10.8a15 15 0 0 0 6.6 6.6l2.2-2.2a1 1 0 0 1 1-.25 11.4 11.4 0 0 0 3.6.57 1 1 0 0 1 1 1V20a1 1 0 0 1-1 1A17 17 0 0 1 3 4a1 1 0 0 1 1-1h3.5a1 1 0 0 1 1 1c0 1.25.2 2.450.57 3.57a1 1 0 0 1-.25 1z"/></svg></span>
        (816) 555-2931
      </li>
      <li class="contacts__item">
        <span class="contacts__icon"><svg viewBox="0 0 24 24"><circle cx="12" cy="12" r="9" fill="none" stroke="#fff" stroke-width="2"/><path d="M3 12h18M12 3c3 3 3 15 0 18M12 3c-3 3-3 15 0 18" fill="none" stroke="#fff" stroke-width="1.6"/></svg></span>
        Verdelynkc.com
      </li>
      <li class="contacts__item">
        <span class="contacts__icon"><svg viewBox="0 0 24 24"><rect x="3" y="6" width="18" height="12" fill="none" stroke="#fff" stroke-width="2"/><path d="M3 6l9 7 9-7" fill="none" stroke="#fff" stroke-width="2"/></svg></span>
        robertfairley@verdelynkc.com
      </li>
      <li class="contacts__item">
        <span class="contacts__icon"></span>
        http://photoreel.com/verdelynkc
      </li>
      <li class="contacts__item">
        <span class="contacts__icon"></span>
        neighborpage.com/VerdelynGardenandGrounds
      </li>
    </ul>
  </div>
</body>
</html>
```